Trifold Leaflet - Osteopathy

Trifold Leaflet (A4 size paper) to provide information and promote an established English seafront osteopathy clinic.
I would like a simple modern design to reflect the seafront location and the caring nature of osteopathy treatment. The design needs to be not be generic or too corporate.
At the top of the front page in a large font should be the word "Osteopathy" as it will be displayed in a rack of leaflets (photo attached) and needs to be eye-catching.
I have attached a logo file and some examples of the kinds of designs that I like- but i'm very open to your expert ideas!
Also attached is a photo of the location- a bit of an ugly building but right on the beach, it would be great if this location could be emphasized!
The Word files: Leaflets word-inside.doc & Leaflets word-outside.doc uploaded show the content that I'd like- this is definitely not set in stone and I appreciate that less content is probably needed. Feel free to include/leave out whatever you feel is right.
More info on the practice can be found on my website:
www.marlowbayosteo.com
The pixelharbor images are ones that I have previously bought the rights to use, but only use them if you think they suit you design- I have included them i case they are of use to you.
Target Market(s)
Any adult.
Industry/Entity Type
Building
Look and feel

```html
<!DOCTYPE html>
<html lang="en">
<head>
<meta charset="utf-8">
<title>Marlow Bay Osteopathy – Leaflet</title>
<link rel="stylesheet" href="https://fonts.googleapis.com/css2?family=Montserrat:wght@700;800&family=Questrial&display=swap">
<style>
:root{
  --bg:#e4e4e4;
  --maroon-dark:#4a1512;
  --maroon:#6e2520;
  --maroon-light:#85322b;
  --red:#c0312a;
  --corner:#a2302a;
  --white:#ffffff;
  --paper:#f2f2f2;
  --steel-light:#b9b9b9;
  --steel:#8e8e8e;
  --ink:#3a3a3a;
}
*{margin:0;padding:0;box-sizing:border-box}
html,body{width:1200px;height:1000px;overflow:hidden;background:var(--bg)}
body{position:relative;font-family:"Questrial",Arial,sans-serif}

.panel{position:absolute;top:90px;width:390px;height:820px;overflow:hidden;box-shadow:0 6px 18px rgba(0,0,0,.18)}

/* Back panel */
.panel--back{left:170px;background:linear-gradient(160deg,var(--maroon-light) 0%,var(--maroon) 45%,var(--maroon-dark) 100%)}
.back__brand{position:absolute;top:330px;left:0;right:0;text-align:center;color:var(--white);font-size:20px;letter-spacing:.5px}
.back__brand .dot{display:inline-block;width:10px;height:10px;border-radius:50%;background:var(--white);margin-right:8px;vertical-align:middle}
.back__intro{position:absolute;top:372px;left:0;width:100%;background:var(--paper);padding:16px 30px;color:var(--red);font-size:13.5px;line-height:1.45}
.back__contact{position:absolute;top:560px;left:70px;color:var(--white);font-size:12.5px;line-height:1.45}
.contact-row{display:flex;align-items:flex-start;gap:12px;margin-bottom:14px}
.contact-row svg{flex:none;margin-top:2px}
.back__web{position:absolute;bottom:48px;left:0;right:0;text-align:center;color:var(--white);font-size:17px;letter-spacing:3px}

/* Front panel */
.panel--front{left:640px;background:linear-gradient(180deg,var(--steel-light) 0%,#a4a4a4 60%,var(--steel) 100%)}
.front__corner{position:absolute;top:0;left:0}
.front__photo{position:absolute;top:80px;right:0;width:250px;height:550px;
  background:linear-gradient(180deg,#757575 0%,#959595 45%,#7e7e7e 100%)}
.front__title{position:absolute;top:28px;left:26px;font-family:"Montserrat",Arial,sans-serif;font-weight:800;font-size:42px;line-height:1;color:var(--white);letter-spacing:.5px;text-shadow:0 2px 3px rgba(0,0,0,.35)}
.front__conditions{position:absolute;top:100px;left:34px;list-style:none;color:var(--ink);font-size:22px;line-height:1.3}
.front__brand{position:absolute;top:440px;left:0;width:230px;background:var(--paper);padding:14px 18px;color:var(--red);font-size:16px}
.front__brand .dot{display:inline-block;width:9px;height:9px;border-radius:50%;background:var(--red);margin-right:7px;vertical-align:middle}
.front__web{position:absolute;bottom:108px;right:24px;font-family:"Montserrat",Arial,sans-serif;font-weight:700;font-size:17px;color:var(--white)}
.front__badges{position:absolute;bottom:30px;left:26px;display:flex;gap:16px}
.badge{width:52px;height:52px;background:rgba(255,255,255,.55)}
.badge--round{border-radius:50%}
</style>
</head>
<body>

<section class="panel panel--back" aria-label="Leaflet back panel">
  <div class="back__brand"><span class="dot"></span>Marlow Bay Osteopathy</div>
  <p class="back__intro">Tom Haverly is an experienced Osteopath, treating a wide variety of joint, muscle and nerve problems. In addition to general osteopathic treatment for back pain and neck pain, he has particular experience in shoulder conditions. He treats a wide range of ages, from children to the elderly. Tom is able to give postural advice.</p>
  <div class="back__contact">
    <div class="contact-row">
      <svg width="14" height="20" viewBox="0 0 14 20" aria-hidden="true"><path d="M7 0a7 7 0 0 0-7 7c0 5 7 13 7 13s7-8 7-13a7 7 0 0 0-7-7z" fill="#fff"/><circle cx="7" cy="7" r="2.6" fill="#6e2520"/></svg>
      <div>Harbour Wellness Centre<br>Esplanade Walk<br>Marlow Bay<br>MB4 2QT</div>
    </div>
    <div class="contact-row">
      <svg width="16" height="16" viewBox="0 0 16 16" aria-hidden="true"><circle cx="8" cy="8" r="7" fill="none" stroke="#fff" stroke-width="1.3"/><path d="M5.3 4.5l1.4 1.6-.8 1c.5 1 1.2 1.7 2.2 2.2l1-.8 1.6 1.4-.9 1.3c-2.6-.4-4.6-2.4-5-5z" fill="#fff"/></svg>
      <div>01632 960418</div>
    </div>
  </div>
  <div class="back__web">www.marlowbayosteo.com</div>
</section>

<section class="panel panel--front" aria-label="Leaflet front panel">
  <div class="front__photo" role="img" aria-label="Photograph of a man seen from behind, holding his lower back in pain"></div>
  <svg class="front__corner" width="60" height="90" viewBox="0 0 60 90" aria-hidden="true"><polygon points="0,0 60,0 0,90" fill="var(--corner)"/></svg>
  <h1 class="front__title">OSTEOPATHY</h1>
  <ul class="front__conditions">
    <li>Arthritis &amp; Joint Pain</li>
    <li>Back &amp; Neck Pain</li>
    <li>Frozen Shoulder</li>
    <li>Sports Injury</li>
    <li>Sciatica</li>
  </ul>
  <div class="front__brand"><span class="dot"></span>Marlow Bay Osteopathy</div>
  <div class="front__web">marlowbayosteo.com</div>
  <div class="front__badges" aria-label="Membership badges">
    <div class="badge"></div>
    <div class="badge badge--round"></div>
  </div>
</section>

</body>
</html>
```